Custom unique Stationary design for Logistics company

We need a custom, unique , elegant and luxurious full stationary design using our new logo, following these guidelines:
1- Business card: double sided, both sides uses the navy blue as the background main color (same as the code of the navy blue used in our logo).
2- envelope and folder: also use the same navy blue as the main background color.
3- book cover( notepad cover) : same thing with the navy blue
4- letterhead: feel free to use the combination of the colors in our logo.
5- rest of the items are up to your creativity

Target Market(s)

corporates and other businesses

Industry/Entity Type

Logistics and heavy machines contractors

Requirements
Must have
• Letterhead, business card, envelope, notepad cover, paper, file
Nice to have
• navy blue to be main background color for business card, envelope, notepad cover

```html
<!DOCTYPE html>
<html lang="en">
<head>
<meta charset="utf-8">
<title>Kestrel Haulage Letterhead</title>
<link href="https://fonts.googleapis.com/css2?family=Lato:wght@400;700&family=Dancing+Script:wght@500&display=swap" rel="stylesheet">
<style>
  :root {
    --navy: #0b4d74;
    --navy-deep: #08405f;
    --orange: #e85a24;
    --ink: #3a3a3a;
    --ink-soft: #555;
    --paper: #ffffff;
    --backdrop: #e4e5e7;
  }
  * { margin: 0; padding: 0; box-sizing: border-box; }
  html, body {
    width: 1200px; height: 960px; overflow: hidden;
    background: var(--backdrop);
    font-family: "Lato", Arial, sans-serif;
    color: var(--ink);
  }
  .letterhead {
    position: absolute;
    left: 282px; top: 30px;
    width: 636px; height: 900px;
    background: var(--paper);
    box-shadow: 0 4px 18px rgba(0,0,0,.12);
    overflow: hidden;
  }
  .brand {
    position: absolute; left: 56px; top: 74px;
    display: flex; align-items: center; gap: 10px;
  }
  .brand-dot {
    width: 16px; height: 16px; border-radius: 50%;
    background: var(--orange);
  }
  .brand-name {
    font-weight: 700; font-size: 26px; letter-spacing: .5px;
    color: var(--navy);
  }
  .contact {
    position: absolute; left: 420px; top: 40px;
    font-size: 10.5px; line-height: 1.45; color: var(--ink);
  }
  .contact-address { margin-bottom: 4px; }
  .contact-row { display: flex; align-items: center; gap: 6px; }
  .contact-row svg { width: 9px; height: 9px; flex: none; }
  .header-rule {
    position: absolute; left: 56px; right: 56px; top: 140px;
    height: 2px; background: var(--navy);
  }
  .letter {
    position: absolute; left: 90px; top: 190px; width: 480px;
    font-size: 12px; line-height: 1.5; color: var(--ink);
  }
  .letter-date { margin-bottom: 18px; }
  .recipient { margin-bottom: 18px; }
  .recipient-block { margin-bottom: 12px; }
  .salutation { font-weight: 700; font-size: 14px; margin-bottom: 14px; }
  .letter p.body { margin-bottom: 14px; color: var(--ink-soft); }
  .closing { margin-top: 18px; color: var(--ink-soft); }
  .signature {
    font-family: "Dancing Script", cursive;
    font-size: 36px; color: #333; margin-top: 8px;
  }
  .footer-swoosh {
    position: absolute; left: 0; bottom: 0;
    width: 636px; height: 900px; pointer-events: none;
  }
</style>
</head>
<body>
  <main class="letterhead">
    <div class="brand">
      <span class="brand-dot"></span>
      <span class="brand-name">KESTREL HAULAGE</span>
    </div>

    <address class="contact" style="font-style:normal">
      <div class="contact-address">Harbor Point 2100 Dock Rd<br>Bayline Ave Suite 310</div>
      <div class="contact-row">
        <svg viewBox="0 0 10 10"><path d="M2 1h2l1 2.5-1.2.8a5 5 0 0 0 2 2l.8-1.2L9 6v2a1 1 0 0 1-1 1A7 7 0 0 1 1 2a1 1 0 0 1 1-1z" fill="var(--navy)"/></svg>
        <span>014 287 3360</span>
      </div>
      <div class="contact-row">
        <svg viewBox="0 0 10 10"><rect x="0.5" y="2" width="9" height="6" rx="1" fill="var(--navy)"/><path d="M1 2.5l4 3 4-3" stroke="#fff" stroke-width=".8" fill="none"/></svg>
        <span>info@kestrelhaulage.com</span>
      </div>
      <div class="contact-row">
        <svg viewBox="0 0 10 10"><circle cx="5" cy="5" r="4.3" fill="var(--navy)"/><path d="M.8 5h8.4M5 .7c-2.4 2.6-2.4 6 0 8.6M5 .7c2.4 2.6 2.4 6 0 8.6" stroke="#fff" stroke-width=".6" fill="none"/></svg>
        <span>www.kestrelhaulage.com</span>
      </div>
    </address>

    <div class="header-rule"></div>

    <article class="letter">
      <div class="letter-date">January-03-2020</div>
      <div class="recipient">
        <div class="recipient-block">Mr, Daniel Reyes<br>President</div>
        <div>Ashford Corporation<br>48 Harbour Lane, Suite# 12<br>Portside, State, 340118</div>
      </div>
      <div class="salutation">Dear Mr, Daniel</div>
      <p class="body">Lorem ipsum dolor sit amet, consectetur adipisicing elit, sed do eiusmod tempor incididunt ut labore et dolore magna aliqua. Ut enim ad minim veniam, quis nostrud exercitation ullamco laboris nisi ut aliquip ex ea commodo consequat. Duis aute irure dolor in reprehenderit in voluptate velit esse cillum dolore eu fugiat nulla pariatur.</p>
      <p class="body">Lorem ipsum dolor sit amet, consectetur adipisicing elit, sed do eiusmod tempor incididunt ut labore et dolore magna aliqua. Ut enim ad minim veniam, quis nostrud exercitation ullamco laboris nisi ut aliquip ex ea commodo consequat. Duis aute irure dolor in reprehenderit in voluptate velit esse cillum dolore eu fugiat nulla pariatur.</p>
      <p class="body">Lorem ipsum dolor sit amet, consectetur adipisicing elit, sed do eiusmod tempor incididunt ut labore et dolore magna aliqua. Ut enim ad minim veniam, quis nostrud exercitation ullamco laboris nisi ut aliquip ex ea commodo consequat.</p>
      <p class="body">Excepteur sint occaecat cupidatat non proident, sunt in culpa qui officia deserunt mollit anim id est laborum. re et dolore magnam aliquam quaerat voluptatem.</p>
      <div class="closing">Regards</div>
      <div class="signature">Adrian Collins</div>
    </article>

    <svg class="footer-swoosh" viewBox="0 0 636 900" aria-hidden="true">
      <path d="M0 900 L0 886 Q360 872 636 752 L636 900 Z" fill="var(--navy)"/>
      <path d="M636 728 L636 742 Q430 842 205 866 Q420 830 636 728 Z" fill="var(--orange)"/>
    </svg>
  </main>
</body>
</html>
```